Business card for a new cabinet shop company named Veloran Cabinets for high end cabinets

Design a business card, thinking dark rich green with colours to speak of high end luxury ie; cream, gold, black possibly

Mitchell Tarrowby
Director Craftsman
Email: info@veloranjoinery-example.com.au
Instagram : @veloran.cabinets

```html
<!DOCTYPE html>
<html lang="en">
<head>
<meta charset="utf-8">
<title>Veloran Cabinets – Business Card</title>
<link href="https://fonts.googleapis.com/css2?family=Poppins:wght@400;500;600;700&display=swap" rel="stylesheet">
<style>
  :root {
    --backdrop: #2a2c2b;
    --card-cream: #f7f1e3;
    --green-deep: #0f3a2b;
    --green-ink: #0c2f23;
    --gold: #c9a75e;
    --on-dark: #f7f1e3;
  }
  * { box-sizing: border-box; margin: 0; padding: 0; }
  html, body {
    width: 1200px; height: 880px; overflow: hidden;
    background: var(--backdrop);
    font-family: "Poppins", sans-serif;
  }
  .canvas { position: relative; width: 1200px; height: 880px; }

  .card {
    position: absolute;
    width: 560px; height: 320px;
    background: var(--card-cream);
    border-radius: 18px;
    overflow: hidden;
    box-shadow: 0 18px 40px rgba(0,0,0,.45);
  }
  .card-front { left: 90px; top: 80px; }
  .card-back { left: 550px; top: 480px; }

  .brand-name {
    font-family: "Poppins", sans-serif;
    font-weight: 500;
    color: var(--gold);
    letter-spacing: .5px;
    white-space: nowrap;
    display: flex; align-items: center; gap: 14px;
    line-height: 1;
  }
  .brand-dot {
    width: 22px; height: 22px; border-radius: 50%;
    background: var(--gold);
    flex: none;
  }
  .card-front .brand-name {
    position: absolute; left: 50%; top: 50%;
    transform: translate(-50%, -50%);
    font-size: 40px;
  }
  .card-back .brand-name {
    position: absolute; left: 40px; top: 120px;
    font-size: 30px;
  }
  .card-back .brand-dot { width: 18px; height: 18px; }

  .swoosh { position: absolute; inset: 0; width: 100%; height: 100%; }

  .person { position: absolute; right: 30px; top: 24px; text-align right; text-align: right; }
  .person-name { font-weight: 700; font-size: 20px; color: var(--green-ink); line-height: 1.15; }
  .person-role { font-weight: 400; font-size: 12px; color: var(--gold); line-height: 1.3; }

  .contact {
    position: absolute; right: 24px; bottom: 26px;
    text-align: right; color: var(--on-dark);
    font-size: 11px; line-height: 1.5;
  }
  .contact-address { margin-bottom: 8px; }
  .contact-line { display: flex; justify-content: flex-end; align-items: center; gap: 8px; }
  .contact-icon {
    width: 14px; height: 14px; border-radius: 50%;
    background: var(--gold);
    display: inline-flex; align-items: center; justify-content: center;
    flex: none;
  }
  .contact-icon svg { width: 9px; height: 9px; }
</style>
</head>
<body>
<main class="canvas">

  <section class="card card-front" aria-label="Card front">
    <div class="brand-name"><span class="brand-dot"></span>Veloran Cabinets</div>
  </section>

  <section class="card card-back" aria-label="Card back">
    <svg class="swoosh" viewBox="0 0 560 320" preserveAspectRatio="none" aria-hidden="true">
      <path d="M560,72 C460,80 400,122 355,200 C315,270 250,296 110,306 L0,308 L0,320 L560,320 Z" fill="var(--green-deep)"/>
      <path d="M520,82 C440,98 392,140 352,212 C316,276 258,298 150,309" fill="none" stroke="var(--card-cream)" stroke-width="3"/>
      <path d="M0,290 C140,288 300,262 330,175 C322,250 250,290 0,302 Z" fill="var(--gold)"/>
    </svg>

    <div class="person">
      <p class="person-name">Mitchell Tarrowby</p>
      <p class="person-role">Director Craftsman</p>
    </div>

    <div class="brand-name"><span class="brand-dot"></span>Veloran Cabinets</div>

    <div class="contact">
      <p class="contact-address">PO BOX 48 Harbour Lane<br>Southbank VIC</p>
      <p class="contact-line">(03) 5550 1842
        <span class="contact-icon"><svg viewBox="0 0 10 10"><path d="M2 1 L4 1 L4.6 3 L3.5 3.8 C4 5 5 6 6.2 6.5 L7 5.4 L9 6 L9 8 C5 8.5 1.5 5 2 1 Z" fill="var(--green-deep)"/></svg></span>
      </p>
      <p class="contact-line">info@veloranjoinery-example.com.au
        <span class="contact-icon"><svg viewBox="0 0 10 10"><rect x="1" y="2.5" width="8" height="5" fill="var(--green-deep)"/><path d="M1 2.5 L5 5.5 L9 2.5" fill="none" stroke="var(--gold)" stroke-width=".8"/></svg></span>
      </p>
      <p class="contact-line">@veloran.cabinets
        <span class="contact-icon"></span>
      </p>
    </div>
  </section>

</main>
</body>
</html>
```